Fabrication and machining company needing printed material designs.

Heron Vessels, Inc. wants to use appealing visuals as well as informative text to tell potential clients about our capabilities in fabrication and machining. We have a new logo to showcase as well as a new website. The use of print media will allow us to leave tangible information with clients, and therefore the design will need to be concise, informative, and visually appealing.

Full Page Flyer (approx. 8.5" x 11"), front and back design. This will be a detailed offering of capabilities and services for our shop.

Half Page Flyer (approx. 5.5" x 8.5"), front and back design. An abbreviated version of the full page flyer, meant to be easily handed out and stored inside a note book.

Bi-fold business card front and back. General offerings of our services. Minimal if any details. Finished size is twice the size of a business card (approx. 4" x 3.5"), once folded in half will be the same size as a standard business card (approx. 2" x 3.5").

Please use www.heronvesselsinc.example for theme ideas. The font used for our logo is ethnocentric, not to be used for all text.

Target Market(s)

Industrial Consumers

Font styles to use
Sans Serif

```html
<!DOCTYPE html>
<html lang="en">
<head>
<meta charset="utf-8">
<title>Heron Vessels, Inc. — Rack Card</title>
<link href="https://fonts.googleapis.com/css2?family=Michroma&family=Roboto+Condensed:wght@400;700&display=swap" rel="stylesheet">
<style>
  :root{
    --orange:#e8822a;
    --charcoal:#3d3d3d;
    --ink:#2a2a2a;
    --paper:#ffffff;
    --backdrop:#dcdcdc;
    --sky:#5aa6e0;
  }
  *{box-sizing:border-box;margin:0;padding:0}
  html,body{width:1200px;height:900px;overflow:hidden;background:var(--backdrop);
    font-family:"Roboto Condensed",Arial,sans-serif;color:var(--ink)}
  ul{list-style:none}
  .card{position:absolute;top:30px;width:420px;height:840px;background:var(--paper);
    box-shadow:0 2px 8px rgba(0,0,0,.18);overflow:hidden}
  .card--front{left:150px;padding:24px}
  .card--back{left:630px}

  /* front */
  .front-photo{position:relative;width:100%;height:100%;
    background:linear-gradient(180deg,var(--sky) 0%,#8fc3ea 35%,#b7bec4 55%,#6d767d 80%,#3f464c 100%)}
  .title-band{position:absolute;left:0;right:0;top:70px;height:150px;background:var(--orange);
    display:flex;align-items:center;padding:0 18px;gap:16px;color:var(--paper)}
  .brand{display:flex;flex-direction:column;align-items:center;gap:8px;width:100px;flex:none}
  .brand__square{width:56px;height:56px;background:var(--paper)}
  .brand__name{font-weight:700;font-size:12px;text-align:center;line-height:1.1}
  .title-band__text h1{font-family:"Michroma",sans-serif;font-size:19px;line-height:1.2;font-weight:400}
  .title-band__text p{font-size:12px;margin-top:8px}

  /* back */
  .panel,.photo{position:absolute}
  .item h3{color:var(--orange);font-size:12px;font-weight:700;line-height:1.15}
  .item li{font-size:10px;line-height:1.2}
  .item li::before{content:"› "}

  .cap-panel{left:0;top:0;width:290px;height:300px;background:var(--charcoal);color:var(--paper);padding:22px 16px}
  .cap-panel h2{font-family:"Michroma",sans-serif;font-size:20px;font-weight:400;margin-bottom:16px;white-space:nowrap}
  .cap-grid{display:grid;grid-template-columns:1fr 1fr;gap:10px 10px}
  .cap-grid .item li{font-size:10.5px}
  .item h3.light{color:var(--paper);font-size:14px}
  .photo--grind{left:290px;top:0;width:130px;height:300px;
    background:linear-gradient(160deg,#5a4a40 0%,#9c6a46 40%,#e6a56a 60%,#4b3a30 100%)}

  .services{left:0;top:300px;width:290px;height:150px;background:var(--orange);color:var(--paper);padding:14px 16px}
  .services h3{font-size:15px;font-weight:700;margin-bottom:6px}
  .services .cols{display:grid;grid-template-columns:1.4fr 1fr;gap:0 8px}
  .services li{font-size:10.5px;line-height:1.3}
  .services li::before{content:"› "}
  .specialities{left:290px;top:300px;width:130px;height:150px;background:var(--paper);padding:12px 12px}

  .photo--skid{left:0;top:450px;width:130px;height:120px;
    background:linear-gradient(135deg,#7a7672 0%,#c2473c 50%,#6e6a66 100%)}
  .photo--weld{left:130px;top:450px;width:290px;height:120px;
    background:linear-gradient(150deg,#2f3f66 0%,#6c6a6a 45%,#f0b070 60%,#3a3230 100%)}

  .lists{left:0;top:570px;width:420px;height:200px;padding:8px 16px;display:flex;gap:10px}
  .lists .col{flex:1;display:flex;flex-direction:column;gap:6px}

  .footer{left:0;top:770px;width:420px;height:70px;background:var(--charcoal);color:var(--paper);
    display:flex;align-items:center;justify-content:space-between;padding:0 16px}
  .brand-inline{display:flex;align-items:center;gap:8px;font-weight:700;font-size:13px;color:var(--orange)}
  .brand-inline .sq{width:26px;height:26px;background:var(--orange)}
  .contact{text-align:right;font-size:10px;line-height:1.35}
  .contact .phone{font-size:17px;font-weight:700;display:flex;align-items:center;gap:5px;justify-content:flex-end}
</style>
</head>
<body>

<section class="card card--front">
  <div class="front-photo" role="img" aria-label="Photo of tall stainless steel storage tanks with catwalk railings against a blue sky">
    <div class="title-band">
      <div class="brand">
        <span class="brand__square"></span>
        <span class="brand__name">Heron Vessels, Inc.</span>
      </div>
      <div class="title-band__text">
        <h1>FABRICATION<br>AND MACHINING</h1>
        <p>ISO 9001 API TANKS 12F, 620, 650 AWWA</p>
      </div>
    </div>
  </div>
</section>

<section class="card card--back">
  <div class="panel cap-panel">
    <h2>CAPABILITIES</h2>
    <div class="cap-grid">
      <div class="item"><h3>Horizontal Lathes</h3><ul><li>Up To 24" Dia &amp; 10' Long</li></ul></div>
      <div class="item"><h3>Vertical Lathes</h3><ul><li>Up To 44" Dia</li></ul></div>
      <div class="item"><h3 class="light">Horizontal Boring Mill Capabilities</h3></div>
      <div class="item"><h3>Press Brake</h3><ul><li>1" Plate 5' Wide</li><li>3/8" Plate x 14' Wide</li></ul></div>
      <div class="item"><h3>CNC Plasma Cutting</h3><ul><li>8' X 20' Capacity</li></ul></div>
      <div class="item"><h3>CNC Roll Forming</h3><ul><li>1/2" X 10' Capacity</li></ul></div>
      <div class="item"><h3>Band Saws</h3><ul><li>22" Cut Capacity</li></ul></div>
      <div class="item"><h3>Iron Workers</h3><ul><li>Up To 85 Tons</li></ul></div>
    </div>
  </div>
  <div class="photo photo--grind" role="img" aria-label="Photo of a grinding machine throwing sparks"></div>

  <div class="panel services">
    <h3>Services</h3>
    <div class="cols">
      <ul><li>Power Generation</li><li>Custom Fabrication</li><li>Pressure vessels</li><li>Tank liners</li><li>Water and Waste Water</li><li>Walkways and Stairs</li></ul>
      <ul><li>Oil &amp; Gas</li><li>Mining</li><li>Tanks</li><li>Piping</li><li>Insulation</li><li>Machining</li></ul>
    </div>
  </div>
  <div class="panel specialities item">
    <h3>Specialities</h3>
    <ul><li>Trailer Components</li><li>Walkways &amp; Stairs</li><li>Fire Tubes</li><li>Pump Skids</li><li>Tank Vents</li><li>Tanks</li><li>Clarifiers</li><li>Piping</li></ul>
  </div>

  <div class="photo photo--skid" role="img" aria-label="Photo of a red pump skid on gravel"></div>
  <div class="photo photo--weld" role="img" aria-label="Photo of a welder at work with sparks flying"></div>

  <div class="panel lists">
    <div class="col">
      <div class="item"><h3>Design and Engineering</h3><ul><li>CAD Drawings</li><li>Engineering Services</li><li>3D Modeling</li></ul></div>
      <div class="item"><h3>Hydraulic Assemblies</h3><ul><li>System Testing</li><li>Hose Assemblies</li><li>Ram Rebuilding</li></ul></div>
    </div>
    <div class="col">
      <div class="item"><h3>Insulating systems</h3><ul><li>Polyurethane Spray Foam</li><li>Metal Wrap</li><li>Heat Trace</li></ul></div>
      <div class="item"><h3>Paint and Corrosion Control</h3><ul><li>Dedicated Paint Bay</li><li>Multi Step Linear Systems</li><li>Stainless Steel Passivation</li><li>Plural Component Application Equip</li><li>Powder Coating</li><li>Galvanizing</li></ul></div>
    </div>
    <div class="col">
      <div class="item"><h3>Welding Processes</h3><ul><li>Carbon Steel</li><li>Stainless Steel</li><li>Aluminum</li></ul></div>
      <div class="item"><h3>Drivelines</h3><ul><li>Custom built</li><li>Rebuilding</li><li>Straightening</li></ul></div>
      <div class="item"><h3>Sandblasting</h3><ul><li>High Production Capacity</li></ul></div>
      <div class="item"><h3>Facility</h3><ul><li>35,000 ft Facility</li><li>5 Acre Storage Yard</li></ul></div>
    </div>
  </div>

  <div class="panel footer">
    <div class="brand-inline"><span class="sq"></span>Heron Vessels, Inc.</div>
    <div class="contact">
      <div>1450 Harbor Rd, Millbrook, UT 84000</div>
      <div>www.heronvesselsinc.example</div>
      <div class="phone">
        <svg width="14" height="14" viewBox="0 0 24 24" aria-hidden="true"><path fill="#fff" d="M6.6 10.8a15 15 0 0 0 6.6 6.6l2.2-2.2c.3-.3.7-.4 1-.2 1.1.4 2.3.6 3.6.6.6 0 1 .4 1 1V20c0 .6-.4 1-1 1A17 17 0 0 1 3 4c0-.6.4-1 1-1h3.5c.6 0 1 .4 1 1 0 1.3.2 2.5.6 3.6.1.3 0 .7-.2 1z"/></svg>
        555-014-2276
      </div>
    </div>
  </div>
</section>

</body>
</html>
```